Business Card

Just need business logo with phone number on it. 0487 312 654
And the following on the bottom of the card.

"Your local plumbing experts".
and emblems for zelpa card, cheque and cash

```html
<!DOCTYPE html>
<html lang="en">
<head>
<meta charset="utf-8">
<title>Kestrel Bay Plumbing &amp; Drainage – Business Card</title>
<link rel="stylesheet" href="https://fonts.googleapis.com/css2?family=Exo+2:wght@400;600;800&display=swap">
<style>
  :root {
    --brand-blue: #1b8fcf;
    --brand-red: #e8202f;
    --ink: #2b2b2b;
    --paper: #ffffff;
    --backdrop: #eceef0;
    --tile-border: #c9ced3;
  }
  * { margin: 0; padding: 0; box-sizing: border-box; }
  html, body {
    width: 1200px; height: 900px; overflow: hidden;
    background: var(--backdrop);
    font-family: "Exo 2", sans-serif;
  }
  .canvas {
    width: 1200px; height: 900px;
    display: flex; flex-direction: column;
    align-items: center; justify-content: center; gap: 40px;
  }
  .card {
    position: relative;
    width: 600px; height: 343px;
    border-radius: 4px;
    overflow: hidden;
    box-shadow: 0 6px 18px rgba(0,0,0,0.15);
  }

  /* Front */
  .card--front {
    background: var(--brand-blue);
    display: flex; align-items: center; justify-content: center;
  }
  .wordmark {
    text-align: center;
    font-weight: 800;
    line-height: 1;
    text-transform: uppercase;
  }
  .wordmark__initials { font-size: 46px; letter-spacing: 2px; }
  .wordmark__name { font-size: 30px; letter-spacing: 1px; margin-top: 4px; }
  .wordmark__trade { font-size: 13px; letter-spacing: 4px; margin-top: 4px; }
  .card--front .wordmark { color: var(--paper); }

  /* Back */
  .card--back { background: var(--paper); }
  .card__wave { position: absolute; inset: 0; width: 600px; height: 343px; }
  .contact {
    position: absolute; left: 42px; top: 42px;
    display: flex; align-items: center; gap: 10px;
    font-size: 21px; font-weight: 400; color: var(--ink);
  }
  .contact__icon { width: 24px; height: 24px; }
  .card--back .wordmark {
    position: absolute; right: 30px; top: 30px;
    color: var(--brand-red);
  }
  .card--back .wordmark__initials { font-size: 34px; }
  .card--back .wordmark__name { font-size: 24px; }
  .card--back .wordmark__trade { font-size: 10.5px; letter-spacing: 3px; }
  .payments {
    position: absolute; right: 28px; top: 146px;
    display: flex; gap: 8px; align-items: center;
  }
  .payment {
    width: 62px; height: 38px; border-radius: 4px;
    display: flex; align-items: center; justify-content: center;
  }
  .payment--card {
    background: var(--paper); border: 1.5px solid var(--tile-border);
    color: var(--brand-blue); font-weight: 800; font-size: 17px;
  }
  .payment--cash { background: #111; }
  .payment--cheque svg, .payment--cash svg { display: block; }
  .tagline {
    position: absolute; left: 42px; top: 180px;
    font-size: 22px; font-weight: 400; color: var(--ink);
    white-space: nowrap;
  }
</style>
</head>
<body>
<main class="canvas">

  <section class="card card--front" aria-label="Card front">
    <div class="wordmark">
      <div class="wordmark__initials">KBPD</div>
      <div class="wordmark__name">Kestrel Bay</div>
      <div class="wordmark__trade">Plumbing &amp; Drainage</div>
    </div>
  </section>

  <section class="card card--back" aria-label="Card back">
    <svg class="card__wave" viewBox="0 0 600 343" aria-hidden="true">
      <path fill="var(--brand-red)" d="M0,268 C160,274 312,242 408,196 C320,252 166,290 0,292 Z"/>
      <path fill="var(--brand-blue)" d="M0,300 C166,298 320,260 420,210 C488,178 546,164 600,160 L600,343 L0,343 Z"/>
    </svg>

    <div class="contact">
      <svg class="contact__icon" viewBox="0 0 24 24" aria-hidden="true">
        <circle cx="12" cy="12" r="11" fill="var(--brand-red)"/>
        <path fill="#fff" d="M6.5 10.5c0-1.5 2.5-3 5.5-3s5.5 1.5 5.5 3v1h-2.5v-1.5h-6v1.5H6.5z M8 12h8l1 4.5H7z"/>
        <circle cx="12" cy="14" r="1.3" fill="var(--brand-red)"/>
      </svg>
      <span class="contact__phone">0487 312 654</span>
    </div>

    <div class="wordmark">
      <div class="wordmark__initials">KBPD</div>
      <div class="wordmark__name">Kestrel Bay</div>
      <div class="wordmark__trade">Plumbing &amp; Drainage</div>
    </div>

    <div class="payments" aria-label="Accepted payments">
      <div class="payment payment--card">zelpa</div>
      <div class="payment payment--cash" aria-label="Cash">
        <svg width="26" height="26" viewBox="0 0 26 26" aria-hidden="true">
          <circle cx="13" cy="13" r="12" fill="#fff"/>
          <text x="13" y="18.5" text-anchor="middle" font-family="Exo 2, sans-serif" font-weight="800" font-size="16" fill="#111">$</text>
        </svg>
      </div>
      <div class="payment payment--cheque" aria-label="Cheque">
        <svg width="62" height="38" viewBox="0 0 62 38" aria-hidden="true">
          <rect x="2" y="6" width="58" height="26" rx="2" fill="#fff" stroke="#333" stroke-width="1.5"/>
          <line x1="8" y1="14" x2="30" y2="14" stroke="#333" stroke-width="1.2"/>
          <line x1="8" y1="20" x2="40" y2="20" stroke="#333" stroke-width="1.2"/>
          <line x1="36" y1="26" x2="54" y2="26" stroke="#333" stroke-width="1.2"/>
          <rect x="44" y="10" width="11" height="6" fill="none" stroke="#333" stroke-width="1.2"/>
        </svg>
      </div>
    </div>

    <p class="tagline">Your local plumbing experts</p>
  </section>

</main>
</body>
</html>
```